Brainwave state designs for neurofeedback report

Design ORIGINAL graphics that correspond with existing colors and shapes for Halo Prism Grid of Stillness & Halo Prism Rhythm Panel for "Normal", "Bright Harbor", "Summit Tide" etc... patterns. You can change the shape of the white outline to be more modern looking. Perhaps you can also use white background with black outline. The frequency bars (can be more ordered) but keep the general shape of the outline.

• An original flair. Modern. Neurotechish
• Do not copy the design. Add your original ideas. Choose a font that complements the design.

```html
<!DOCTYPE html>
<html lang="en">
<head>
<meta charset="utf-8">
<title>Patterns of Mind</title>
<link href="https://fonts.googleapis.com/css2?family=Poppins:wght@300;400;500;800&display=swap" rel="stylesheet">
<style>
  :root {
    --ink: #1f2228;
    --paper: #ffffff;
    --field: #c3c9d3;
    --ring: #e4e8ee;
    --red: #d8372c;
    --crimson: #c42f2a;
    --pink: #ef5a98;
    --magenta: #b03aa8;
    --orange: #f26a3c;
    --rust: #e35f36;
    --amber: #fbb338;
    --yellow: #f4e84a;
    --green: #1a4a24;
    --blue: #8a9ed6;
    --violet: #8a5aa8;
  }
  html, body { margin: 0; padding: 0; width: 1200px; height: 848px; overflow: hidden; background: var(--paper); }
  .canvas { width: 1200px; height: 848px; display: block; font-family: "Poppins", sans-serif; }
  .title { font-size: 68px; fill: var(--ink); letter-spacing: -1px; }
  .title .light { font-weight: 300; }
  .title .heavy { font-weight: 800; }
  .chart-name { font-size: 20px; font-weight: 400; fill: var(--ink); text-anchor: middle; }
  .chart-name.small { font-size: 18px; }
  .hz { font-size: 11px; font-weight: 500; fill: var(--ink); text-anchor: middle; dominant-baseline: central; }
  .hz.small { font-size: 9.5px; }
  .tick-label { font-size: 11px; fill: var(--ink); text-anchor: middle; }
  .axis { stroke: var(--ink); stroke-width: 1.2; fill: none; stroke-linecap: round; }
  .tick { fill: var(--ink); }
  .field { fill: url(#dot-field); }
  .ring { fill: none; stroke: var(--ring); stroke-width: 1; }
  .void { fill: var(--paper); }
  .outline { fill: none; stroke: var(--ink); stroke-width: 1.6; stroke-linejoin: round; stroke-linecap: round; }
  .outline.void { fill: var(--paper); }
  .node { fill: var(--paper); stroke: var(--ink); stroke-width: 1.6; }
  .chart rect { rx: 2.5px; ry: 2.5px; }
  .chart rect.void { rx: 0; ry: 0; }
  .red { fill: var(--red); } .crimson { fill: var(--crimson); } .pink { fill: var(--pink); }
  .magenta { fill: var(--magenta); } .orange { fill: var(--orange); } .rust { fill: var(--rust); }
  .amber { fill: var(--amber); } .yellow { fill: var(--yellow); } .green { fill: var(--green); }
  .blue { fill: var(--blue); } .violet { fill: var(--violet); }
</style>
</head>
<body>
<svg class="canvas" viewBox="0 0 1500 1060" width="1200" height="848" xmlns="http://www.w3.org/2000/svg">
  <defs>
    <pattern id="dot-field" width="7" height="7" patternUnits="userSpaceOnUse">
      <circle cx="3.5" cy="3.5" r="1" fill="#c3c9d3"/>
    </pattern>
    <g id="axis-wide">
      <path class="axis" d="M-185 523 H-14 M14 523 H183"/>
      <g class="tick"><circle cx="-14" cy="523" r="2.5"/><circle cx="-44" cy="523" r="2.5"/><circle cx="-76" cy="523" r="2.5"/><circle cx="-108" cy="523" r="2.5"/><circle cx="-139" cy="523" r="2.5"/><circle cx="-170" cy="523" r="2.5"/><circle cx="14" cy="523" r="2.5"/><circle cx="40" cy="523" r="2.5"/><circle cx="71" cy="523" r="2.5"/><circle cx="103" cy="523" r="2.5"/><circle cx="134" cy="523" r="2.5"/><circle cx="165" cy="523" r="2.5"/></g>
      <text class="tick-label" x="-170" y="546">20.0</text><text class="tick-label" x="-139" y="546">16.0</text><text class="tick-label" x="-108" y="546">12.0</text><text class="tick-label" x="-76" y="546">8.0</text><text class="tick-label" x="-44" y="546">4.0</text>
      <text class="tick-label" x="40" y="546">4.0</text><text class="tick-label" x="71" y="546">8.0</text><text class="tick-label" x="103" y="546">12.0</text><text class="tick-label" x="134" y="546">16.0</text><text class="tick-label" x="165" y="546">20.0</text>
    </g>
    <g id="axis-narrow">
      <path class="axis" d="M-162 933 H-12 M12 933 H162"/>
      <g class="tick"><circle cx="-12" cy="933" r="2.3"/><circle cx="-39" cy="933" r="2.3"/><circle cx="-66" cy="933" r="2.3"/><circle cx="-93" cy="933" r="2.3"/><circle cx="-119" cy="933" r="2.3"/><circle cx="-146" cy="933" r="2.3"/><circle cx="12" cy="933" r="2.3"/><circle cx="39" cy="933" r="2.3"/><circle cx="66" cy="933" r="2.3"/><circle cx="93" cy="933" r="2.3"/><circle cx="119" cy="933" r="2.3"/><circle cx="146" cy="933" r="2.3"/></g>
      <text class="tick-label" x="-146" y="952">12.5</text><text class="tick-label" x="-119" y="952">9.6</text><text class="tick-label" x="-93" y="952">7.2</text><text class="tick-label" x="-66" y="952">4.8</text><text class="tick-label" x="-39" y="952">2.4</text>
      <text class="tick-label" x="39" y="952">2.4</text><text class="tick-label" x="66" y="952">4.8</text><text class="tick-label" x="93" y="952">7.2</text><text class="tick-label" x="119" y="952">9.6</text><text class="tick-label" x="146" y="952">12.5</text>
    </g>
    <g id="scale-wide">
      <text class="hz" y="211">40</text><text class="hz" y="230">38</text><text class="hz" y="248">30</text><text class="hz" y="266">24</text><text class="hz" y="285">19</text><text class="hz" y="303">15</text><text class="hz" y="321">12.5</text><text class="hz" y="340">10.5</text><text class="hz" y="358">9</text><text class="hz" y="376">7.5</text><text class="hz" y="395">6</text><text class="hz" y="413">4</text><text class="hz" y="431">3</text><text class="hz" y="450">1.5</text><text class="hz" y="468">0.75</text>
    </g>
    <g id="scale-narrow">
      <text class="hz small" y="652">91</text><text class="hz small" y="666">79</text><text class="hz small" y="680">69</text><text class="hz small" y="694">59</text><text class="hz small" y="708">49</text><text class="hz small" y="722">38</text><text class="hz small" y="736">30</text><text class="hz small" y="750">24</text><text class="hz small" y="764">19</text><text class="hz small" y="778">15</text><text class="hz small" y="792">12.5</text><text class="hz small" y="806">10.5</text><text class="hz small" y="820">9</text><text class="hz small" y="834">7.5</text><text class="hz small" y="848">6</text><text class="hz small" y="862">4</text><text class="hz small" y="876">3</text><text class="hz small" y="890">1.5</text><text class="hz small" y="904">0.75</text>
    </g>
  </defs>

  <text class="title" x="88" y="148"><tspan class="light">PATTERNS </tspan><tspan class="heavy">OF MIND</tspan></text>

  <!-- Ordinary Mind -->
  <g class="chart" transform="translate(260 0)">
    <circle class="ring" cx="0" cy="340" r="160"/>
    <ellipse class="field" cx="0" cy="338" rx="132" ry="140"/>
    <path class="void" d="M-110 196 C-70 280 -70 400 -88 482 L87 482 C70 400 70 280 112 196 Z"/>
    <path class="outline" d="M-110 204 C-70 280 -70 400 -88 478 M112 204 C70 280 70 400 87 478"/>
    <circle class="node" cx="-110" cy="204" r="3.5"/><circle class="node" cx="112" cy="204" r="3.5"/>
    <circle class="node" cx="-88" cy="478" r="3.5"/><circle class="node" cx="87" cy="478" r="3.5"/>
    <rect class="orange" x="-62" y="205" width="48" height="13"/><rect class="orange" x="14" y="205" width="47" height="13"/>
    <rect class="orange" x="-62" y="224" width="48" height="13"/><rect class="orange" x="14" y="224" width="47" height="13"/>
    <rect class="rust" x="-82" y="242" width="68" height="13"/><rect class="rust" x="14" y="242" width="68" height="13"/>
    <rect class="orange" x="-75" y="260" width="61" height="13"/><rect class="orange" x="14" y="260" width="60" height="13"/>
    <rect class="amber" x="-70" y="279" width="56" height="13"/><rect class="amber" x="14" y="279" width="55" height="13"/>
    <rect class="yellow" x="-65" y="297" width="51" height="13"/><rect class="yellow" x="14" y="297" width="50" height="13"/>
    <rect class="green" x="-59" y="315" width="45" height="13"/><rect class="green" x="14" y="315" width="45" height="13"/>
    <rect class="green" x="-52" y="334" width="38" height="13"/><rect class="green" x="14" y="334" width="37" height="13"/>
    <rect class="green" x="-46" y="352" width="32" height="13"/><rect class="green" x="14" y="352" width="32" height="13"/>
    <rect class="blue" x="-42" y="370" width="28" height="13"/><rect class="blue" x="14" y="370" width="28" height="13"/>
    <rect class="blue" x="-44" y="389" width="30" height="13"/><rect class="blue" x="14" y="389" width="30" height="13"/>
    <rect class="blue" x="-38" y="407" width="24" height="13"/><rect class="blue" x="14" y="407" width="24" height="13"/>
    <rect class="violet" x="-37" y="425" width="23" height="13"/><rect class="violet" x="14" y="425" width="23" height="13"/>
    <rect class="violet" x="-44" y="444" width="30" height="13"/><rect class="violet" x="14" y="444" width="30" height="13"/>
    <rect class="violet" x="-53" y="462" width="39" height="13"/><rect class="violet" x="14" y="462" width="39" height="13"/>
    <use href="#scale-wide"/>
    <use href="#axis-wide"/>
    <text class="chart-name" x="0" y="583">Ordinary Mind</text>
  </g>

  <!-- Bright Harbor -->
  <g class="chart" transform="translate(750 0)">
    <circle class="ring" cx="0" cy="340" r="178"/>
    <ellipse class="field" cx="0" cy="338" rx="175" ry="145"/>
    <path class="outline void" d="M-88 482 C-118 450 -112 410 -120 385 C-126 368 -168 370 -165 340 C-160 290 -110 220 -60 200 C-10 182 50 190 90 225 C130 262 165 310 160 345 C155 372 110 370 104 400 C98 440 100 465 66 482 Z"/>
    <circle class="node" cx="-165" cy="340" r="3.5"/><circle class="node" cx="160" cy="345" r="3.5"/>
    <circle class="node" cx="-88" cy="482" r="3.5"/><circle class="node" cx="66" cy="482" r="3.5"/>
    <rect class="orange" x="-39" y="205" width="25" height="13"/><rect class="orange" x="14" y="205" width="14" height="13"/>
    <rect class="orange" x="-41" y="224" width="27" height="13"/><rect class="orange" x="14" y="224" width="14" height="13"/>
    <rect class="rust" x="-43" y="242" width="29" height="13"/><rect class="rust" x="14" y="242" width="16" height="13"/>
    <rect class="orange" x="-50" y="260" width="36" height="13"/><rect class="orange" x="14" y="260" width="30" height="13"/>
    <rect class="amber" x="-60" y="279" width="46" height="13"/><rect class="amber" x="14" y="279" width="42" height="13"/>
    <rect class="yellow" x="-59" y="297" width="45" height="13"/><rect class="yellow" x="14" y="297" width="53" height="13"/>
    <rect class="green" x="-66" y="315" width="52" height="13"/><rect class="green" x="14" y="315" width="74" height="13"/>
    <rect class="green" x="-94" y="334" width="80" height="13"/><rect class="green" x="14" y="334" width="82" height="13"/>
    <rect class="green" x="-148" y="352" width="134" height="13"/><rect class="green" x="14" y="352" width="134" height="13"/>
    <rect class="blue" x="-64" y="370" width="50" height="13"/><rect class="blue" x="14" y="370" width="57" height="13"/>
    <rect class="blue" x="-74" y="389" width="60" height="13"/><rect class="blue" x="14" y="389" width="63" height="13"/>
    <rect class="blue" x="-64" y="407" width="50" height="13"/><rect class="blue" x="14" y="407" width="58" height="13"/>
    <rect class="violet" x="-68" y="425" width="54" height="13"/><rect class="violet" x="14" y="425" width="59" height="13"/>
    <rect class="violet" x="-66" y="444" width="52" height="13"/><rect class="violet" x="14" y="444" width="78" height="13"/>
    <rect class="violet" x="-92" y="462" width="78" height="13"/><rect class="violet" x="14" y="462" width="51" height="13"/>
    <use href="#scale-wide"/>
    <use href="#axis-wide"/>
    <text class="chart-name" x="0" y="580">Bright Harbor</text>
  </g>

  <!-- Summit Tide -->
  <g class="chart" transform="translate(1241 0)">
    <circle class="ring" cx="0" cy="340" r="180"/>
    <ellipse class="field" cx="0" cy="340" rx="175" ry="150"/>
    <circle class="outline void" cx="0" cy="340" r="150"/>
    <circle class="node" cx="-150" cy="340" r="3.5"/><circle class="node" cx="150" cy="340" r="3.5"/>
    <circle class="node" cx="0" cy="190" r="3.5"/><circle class="node" cx="0" cy="490" r="3.5"/>
    <rect class="orange" x="-64" y="205" width="50" height="13"/><rect class="orange" x="14" y="205" width="49" height="13"/>
    <rect class="orange" x="-64" y="224" width="50" height="13"/><rect class="orange" x="14" y="224" width="49" height="13"/>
    <rect class="rust" x="-42" y="242" width="28" height="13"/><rect class="rust" x="14" y="242" width="74" height="13"/>
    <rect class="orange" x="-71" y="260" width="57" height="13"/><rect class="orange" x="14" y="260" width="66" height="13"/>
    <rect class="amber" x="-86" y="279" width="72" height="13"/><rect class="amber" x="14" y="279" width="60" height="13"/>
    <rect class="yellow" x="-60" y="297" width="46" height="13"/><rect class="yellow" x="14" y="297" width="53" height="13"/>
    <rect class="green" x="-75" y="315" width="61" height="13"/><rect class="green" x="14" y="315" width="74" height="13"/>
    <rect class="green" x="-127" y="334" width="113" height="13"/><rect class="green" x="14" y="334" width="82" height="13"/>
    <rect class="green" x="-83" y="352" width="69" height="13"/><rect class="green" x="14" y="352" width="118" height="13"/>
    <rect class="blue" x="-74" y="370" width="60" height="13"/><rect class="blue" x="14" y="370" width="62" height="13"/>
    <rect class="blue" x="-74" y="389" width="60" height="13"/><rect class="blue" x="14" y="389" width="63" height="13"/>
    <rect class="blue" x="-64" y="407" width="50" height="13"/><rect class="blue" x="14" y="407" width="82" height="13"/>
    <rect class="violet" x="-74" y="425" width="60" height="13"/><rect class="violet" x="14" y="425" width="72" height="13"/>
    <rect class="violet" x="-100" y="444" width="86" height="13"/><rect class="violet" x="14" y="444" width="64" height="13"/>
    <rect class="violet" x="-57" y="462" width="43" height="13"/><rect class="violet" x="14" y="462" width="50" height="13"/>
    <use href="#scale-wide"/>
    <use href="#axis-wide"/>
    <text class="chart-name" x="0" y="580">Summit Tide</text>
  </g>

  <!-- Universal Consciousness, rounded -->
  <g class="chart" transform="translate(239 0)">
    <circle class="ring" cx="0" cy="772" r="160"/>
    <ellipse class="field" cx="0" cy="772" rx="158" ry="142"/>
    <path class="outline void" d="M0 914 C-80 912 -140 860 -140 785 C-140 700 -75 630 0 630 C75 630 140 700 140 785 C140 860 80 912 0 914 Z"/>
    <circle class="node" cx="-140" cy="785" r="3.2"/><circle class="node" cx="140" cy="785" r="3.2"/>
    <circle class="node" cx="0" cy="914" r="3.2"/>
    <rect class="red" x="-25" y="633" width="13" height="10"/><rect class="red" x="12" y="633" width="18" height="10"/>
    <rect class="red" x="-25" y="647" width="13" height="10"/><rect class="red" x="12" y="647" width="20" height="10"/>
    <rect class="red" x="-28" y="661" width="16" height="10"/><rect class="red" x="12" y="661" width="27" height="10"/>
    <rect class="crimson" x="-34" y="675" width="22" height="10"/><rect class="crimson" x="12" y="675" width="32" height="10"/>
    <rect class="pink" x="-43" y="689" width="31" height="10"/><rect class="pink" x="12" y="689" width="34" height="10"/>
    <rect class="magenta" x="-52" y="703" width="40" height="10"/><rect class="magenta" x="12" y="703" width="46" height="10"/>
    <rect class="orange" x="-85" y="717" width="73" height="10"/><rect class="orange" x="12" y="717" width="53" height="10"/>
    <rect class="rust" x="-85" y="731" width="73" height="10"/><rect class="rust" x="12" y="731" width="62" height="10"/>
    <rect class="orange" x="-78" y="745" width="66" height="10"/><rect class="orange" x="12" y="745" width="66" height="10"/>
    <rect class="amber" x="-78" y="759" width="66" height="10"/><rect class="amber" x="12" y="759" width="66" height="10"/>
    <rect class="yellow" x="-89" y="773" width="77" height="10"/><rect class="yellow" x="12" y="773" width="77" height="10"/>
    <rect class="green" x="-99" y="787" width="87" height="10"/><rect class="green" x="12" y="787" width="75" height="10"/>
    <rect class="green" x="-101" y="801" width="89" height="10"/><rect class="green" x="12" y="801" width="89" height="10"/>
    <rect class="green" x="-102" y="815" width="90" height="10"/><rect class="green" x="12" y="815" width="90" height="10"/>
    <rect class="blue" x="-82" y="829" width="70" height="10"/><rect class="blue" x="12" y="829" width="72" height="10"/>
    <rect class="blue" x="-79" y="843" width="67" height="10"/><rect class="blue" x="12" y="843" width="67" height="10"/>
    <rect class="blue" x="-75" y="857" width="63" height="10"/><rect class="blue" x="12" y="857" width="62" height="10"/>
    <rect class="violet" x="-57" y="871" width="45" height="10"/><rect class="violet" x="12" y="871" width="45" height="10"/>
    <rect class="violet" x="-43" y="885" width="31" height="10"/><rect class="violet" x="12" y="885" width="31" height="10"/>
    <rect class="violet" x="-37" y="899" width="25" height="10"/><rect class="violet" x="12" y="899" width="39" height="10"/>
    <text class="hz small" y="638">100</text>
    <use href="#scale-narrow"/>
    <use href="#axis-narrow"/>
    <text class="chart-name small" x="0" y="994">Universal Consiousness</text>
  </g>

  <!-- Universal Consciousness, rising -->
  <g class="chart" transform="translate(576 0)">
    <circle class="ring" cx="0" cy="772" r="148"/>
    <ellipse class="field" cx="0" cy="772" rx="135" ry="142"/>
    <path class="outline void" d="M-16 628 C-18 690 -18 730 -26 748 C-50 770 -70 800 -78 830 C-88 860 -128 870 -124 900 C-122 912 -110 914 -100 914 L78 914 C96 914 100 890 94 870 C88 840 80 818 60 805 C40 790 28 770 24 740 C20 700 18 660 16 628 Z"/>
    <circle class="node" cx="-16" cy="628" r="3.2"/><circle class="node" cx="16" cy="628" r="3.2"/>
    <circle class="node" cx="-124" cy="900" r="3.2"/><circle class="node" cx="94" cy="870" r="3.2"/>
    <rect class="red" x="-14" y="633" width="2" height="10"/><rect class="red" x="12" y="633" width="3" height="10"/>
    <rect class="red" x="-14" y="647" width="2" height="10"/><rect class="red" x="12" y="647" width="3" height="10"/>
    <rect class="red" x="-14" y="661" width="2" height="10"/><rect class="red" x="12" y="661" width="3" height="10"/>
    <rect class="crimson" x="-15" y="675" width="3" height="10"/><rect class="crimson" x="12" y="675" width="3" height="10"/>
    <rect class="pink" x="-15" y="689" width="3" height="10"/><rect class="pink" x="12" y="689" width="4" height="10"/>
    <rect class="magenta" x="-19" y="703" width="7" height="10"/><rect class="magenta" x="12" y="703" width="5" height="10"/>
    <rect class="orange" x="-18" y="717" width="6" height="10"/><rect class="orange" x="12" y="717" width="8" height="10"/>
    <rect class="rust" x="-19" y="731" width="7" height="10"/><rect class="rust" x="12" y="731" width="10" height="10"/>
    <rect class="orange" x="-28" y="745" width="16" height="10"/><rect class="orange" x="12" y="745" width="18" height="10"/>
    <rect class="amber" x="-48" y="759" width="36" height="10"/><rect class="amber" x="12" y="759" width="24" height="10"/>
    <rect class="yellow" x="-62" y="773" width="50" height="10"/><rect class="yellow" x="12" y="773" width="34" height="10"/>
    <rect class="green" x="-62" y="787" width="50" height="10"/><rect class="green" x="12" y="787" width="40" height="10"/>
    <rect class="green" x="-78" y="801" width="66" height="10"/><rect class="green" x="12" y="801" width="35" height="10"/>
    <rect class="green" x="-64" y="815" width="52" height="10"/><rect class="green" x="12" y="815" width="72" height="10"/>
    <rect class="blue" x="-68" y="829" width="56" height="10"/><rect class="blue" x="12" y="829" width="57" height="10"/>
    <rect class="blue" x="-69" y="843" width="57" height="10"/><rect class="blue" x="12" y="843" width="60" height="10"/>
    <rect class="blue" x="-74" y="857" width="62" height="10"/><rect class="blue" x="12" y="857" width="69" height="10"/>
    <rect class="violet" x="-104" y="871" width="92" height="10"/><rect class="violet" x="12" y="871" width="76" height="10"/>
    <rect class="violet" x="-118" y="885" width="106" height="10"/><rect class="violet" x="12" y="885" width="70" height="10"/>
    <rect class="violet" x="-110" y="899" width="98" height="10"/><rect class="violet" x="12" y="899" width="62" height="10"/>
    <text class="hz small" y="638">100</text>
    <use href="#scale-narrow"/>
    <use href="#axis-narrow"/>
    <text class="chart-name small" x="0" y="994">Universal Consiousness</text>
  </g>

  <!-- Superconscious mind -->
  <g class="chart" transform="translate(927 0)">
    <circle class="ring" cx="0" cy="772" r="140"/>
    <ellipse class="field" cx="0" cy="772" rx="122" ry="142"/>
    <path class="outline void" d="M-34 628 C-50 680 -64 740 -74 775 C-86 800 -74 818 -62 830 C-72 860 -84 890 -88 914 L88 914 C82 890 72 860 64 830 C80 815 96 800 84 790 C70 775 55 760 40 730 C28 700 20 660 18 628 Z"/>
    <circle class="node" cx="-34" cy="628" r="3.2"/><circle class="node" cx="18" cy="628" r="3.2"/>
    <circle class="node" cx="-88" cy="914" r="3.2"/><circle class="node" cx="88" cy="914" r="3.2"/>
    <rect class="red" x="-14" y="633" width="2" height="10"/><rect class="red" x="12" y="633" width="2" height="10"/>
    <rect class="red" x="-14" y="647" width="2" height="10"/><rect class="red" x="12" y="647" width="2" height="10"/>
    <rect class="red" x="-15" y="661" width="3" height="10"/><rect class="red" x="12" y="661" width="2" height="10"/>
    <rect class="crimson" x="-15" y="675" width="3" height="10"/><rect class="crimson" x="12" y="675" width="2" height="10"/>
    <rect class="pink" x="-16" y="689" width="4" height="10"/><rect class="pink" x="12" y="689" width="2" height="10"/>
    <rect class="magenta" x="-38" y="703" width="26" height="10"/><rect class="magenta" x="12" y="703" width="5" height="10"/>
    <rect class="orange" x="-38" y="717" width="26" height="10"/><rect class="orange" x="12" y="717" width="25" height="10"/>
    <rect class="rust" x="-38" y="731" width="26" height="10"/><rect class="rust" x="12" y="731" width="26" height="10"/>
    <rect class="orange" x="-57" y="745" width="45" height="10"/><rect class="orange" x="12" y="745" width="44" height="10"/>
    <rect class="amber" x="-38" y="759" width="26" height="10"/><rect class="amber" x="12" y="759" width="37" height="10"/>
    <rect class="yellow" x="-57" y="773" width="45" height="10"/><rect class="yellow" x="12" y="773" width="47" height="10"/>
    <rect class="green" x="-50" y="787" width="38" height="10"/><rect class="green" x="12" y="787" width="38" height="10"/>
    <rect class="green" x="-79" y="801" width="67" height="10"/><rect class="green" x="12" y="801" width="67" height="10"/>
    <rect class="green" x="-44" y="815" width="32" height="10"/><rect class="green" x="12" y="815" width="32" height="10"/>
    <rect class="blue" x="-30" y="829" width="18" height="10"/><rect class="blue" x="12" y="829" width="18" height="10"/>
    <rect class="blue" x="-27" y="843" width="15" height="10"/><rect class="blue" x="12" y="843" width="15" height="10"/>
    <rect class="blue" x="-42" y="857" width="30" height="10"/><rect class="blue" x="12" y="857" width="30" height="10"/>
    <rect class="violet" x="-47" y="871" width="35" height="10"/><rect class="violet" x="12" y="871" width="35" height="10"/>
    <rect class="violet" x="-59" y="885" width="47" height="10"/><rect class="violet" x="12" y="885" width="47" height="10"/>
    <rect class="violet" x="-68" y="899" width="56" height="10"/><rect class="violet" x="12" y="899" width="56" height="10"/>
    <text class="hz small" y="638">100</text>
    <use href="#scale-narrow"/>
    <use href="#axis-narrow"/>
    <text class="chart-name small" x="0" y="994">Superconscious mind</text>
  </g>

  <!-- OBE -->
  <g class="chart" transform="translate(1273 0)">
    <circle class="ring" cx="0" cy="775" r="138"/>
    <ellipse class="field" cx="0" cy="775" rx="118" ry="128"/>
    <rect class="void" x="-63" y="630" width="126" height="285"/>
    <path class="outline" d="M-63 636 V912 M63 636 V912"/>
    <circle class="node" cx="-63" cy="636" r="3.2"/><circle class="node" cx="63" cy="636" r="3.2"/>
    <circle class="node" cx="-63" cy="912" r="3.2"/><circle class="node" cx="63" cy="912" r="3.2"/>
    <rect class="red" x="-15" y="647" width="3" height="10"/><rect class="red" x="12" y="647" width="3" height="10"/>
    <rect class="red" x="-15" y="661" width="3" height="10"/><rect class="red" x="12" y="661" width="3" height="10"/>
    <rect class="crimson" x="-15" y="675" width="3" height="10"/><rect class="crimson" x="12" y="675" width="3" height="10"/>
    <rect class="pink" x="-15" y="689" width="3" height="10"/><rect class="pink" x="12" y="689" width="3" height="10"/>
    <rect class="magenta" x="-16" y="703" width="4" height="10"/><rect class="magenta" x="12" y="703" width="3" height="10"/>
    <rect class="orange" x="-16" y="717" width="4" height="10"/><rect class="orange" x="12" y="717" width="3" height="10"/>
    <rect class="rust" x="-16" y="731" width="4" height="10"/><rect class="rust" x="12" y="731" width="3" height="10"/>
    <rect class="orange" x="-16" y="745" width="4" height="10"/><rect class="orange" x="12" y="745" width="3" height="10"/>
    <rect class="amber" x="-16" y="759" width="4" height="10"/><rect class="amber" x="12" y="759" width="3" height="10"/>
    <rect class="yellow" x="-16" y="773" width="4" height="10"/><rect class="yellow" x="12" y="773" width="3" height="10"/>
    <rect class="green" x="-15" y="787" width="3" height="10"/><rect class="green" x="12" y="787" width="3" height="10"/>
    <rect class="green" x="-15" y="801" width="3" height="10"/><rect class="green" x="12" y="801" width="3" height="10"/>
    <rect class="green" x="-15" y="815" width="3" height="10"/><rect class="green" x="12" y="815" width="3" height="10"/>
    <rect class="blue" x="-16" y="829" width="4" height="10"/><rect class="blue" x="12" y="829" width="3" height="10"/>
    <rect class="blue" x="-16" y="843" width="4" height="10"/><rect class="blue" x="12" y="843" width="3" height="10"/>
    <rect class="blue" x="-16" y="857" width="4" height="10"/><rect class="blue" x="12" y="857" width="3" height="10"/>
    <rect class="violet" x="-20" y="871" width="8" height="10"/><rect class="violet" x="12" y="871" width="8" height="10"/>
    <rect class="violet" x="-29" y="885" width="17" height="10"/><rect class="violet" x="12" y="885" width="20" height="10"/>
    <rect class="violet" x="-34" y="899" width="22" height="10"/><rect class="violet" x="12" y="899" width="22" height="10"/>
    <use href="#scale-narrow"/>
    <use href="#axis-narrow"/>
    <text class="chart-name small" x="0" y="994">OBE (Out of Body Experience)</text>
  </g>
</svg>
</body>
</html>
```